Meridian Crestline Motors *

Professional business cards for our auto wholesale dealership.

Target Market(s)

New and used cars sales managers and middle class to higher end private party buyers.

Industry/Entity Type

Automotive

Contact Information for Business Card

Meridian Crestline Motors
Darnell R Okonski
Owner
(555) 304-6618
mercrestmotors@quillbox.example
Dealer Lic # 48265

Logo Text

Meridian Crestline Motors, Mer Crest Motors, MCM, etc

Font styles to use
Serif
Sans Serif

Colors

Designer to choose colors to be used in the design.

Requirements
Must have
• A professional, but not pretentious, look
Nice to have
• It might be nice to see "MCM" in a shape form i.e. circle, triangle, etc in the corner or background somehwere
Should not have
• bright "girly" colors

```html
<!DOCTYPE html>
<html lang="en">
<head>
<meta charset="utf-8">
<title>Meridian Crestline Motors – Business Card</title>
<link rel="stylesheet" href="https://fonts.googleapis.com/css2?family=Open+Sans:wght@400;600;700;800&display=swap">
<style>
  :root {
    --backdrop: #3b3e42;
    --card-top: #2c323a;
    --card-bottom: #1b1f25;
    --lime-light: #c9e21a;
    --lime-dark: #8fb516;
    --lime-ring: #7d9e12;
    --ink-dark: #1d2228;
    --text-light: #f2f3f4;
  }
  * { box-sizing: border-box; margin: 0; padding: 0; }
  html, body {
    width: 1200px; height: 1200px; overflow: hidden;
    background: var(--backdrop);
    font-family: "Open Sans", Arial, sans-serif;
  }
  .card {
    position: absolute; left: 250px; width: 700px; height: 400px;
    border-radius: 22px; overflow: hidden;
    background: radial-gradient(ellipse at 45% 35%, var(--card-top), var(--card-bottom) 75%);
    box-shadow: 0 14px 30px rgba(0,0,0,.35);
  }
  .card--front { top: 130px; }
  .card--back { top: 630px; }

  .lime-edge {
    position: absolute; left: 0; bottom: 0; height: 26px; width: 78%;
    background: linear-gradient(90deg, var(--lime-dark), var(--lime-light));
    border-top-right-radius: 20px;
  }

  .brand-mark {
    position: absolute; border-radius: 50%;
    background: radial-gradient(circle at 40% 35%, var(--lime-light), var(--lime-dark));
    box-shadow: 0 0 0 3px var(--card-bottom), 0 0 0 5px var(--lime-ring);
  }
  .card--front .brand-mark { width: 140px; height: 140px; left: 500px; top: 62px; }

  .wordmark {
    position: absolute; left: 70px; top: 200px; color: var(--text-light);
    font-weight: 800; line-height: 1;
  }
  .wordmark__main { font-size: 62px; letter-spacing: 2px; }
  .wordmark__sub { font-size: 34px; font-weight: 700; margin-top: 8px; margin-left: 4px; }

  .card--back .brand-mark { width: 150px; height: 150px; left: 70px; top: 60px; }
  .monogram {
    position: absolute; left: 92px; top: 232px; width: 106px; text-align: center;
    color: var(--text-light); font-weight: 800; font-size: 30px; letter-spacing: 3px;
  }

  .name-tab {
    position: absolute; right: 0; top: 64px; width: 300px; height: 86px;
    background: linear-gradient(90deg, var(--lime-light), var(--lime-dark));
    border-radius: 22px 0 0 22px;
    padding: 12px 0 0 28px; color: var(--ink-dark);
  }
  .name-tab__name { font-size: 25px; font-weight: 700; line-height: 1.2; }
  .name-tab__role { font-size: 18px; font-weight: 600; margin-left: 70px; }

  .contact-list {
    position: absolute; right: 40px; top: 182px; list-style: none;
    color: var(--text-light); font-size: 20px; text-align: right;
  }
  .contact-list li {
    display: flex; justify-content: flex-end; align-items: center;
    height: 42px; gap: 14px;
  }
  .contact-list svg { width: 22px; height: 22px; flex: none; }
  .contact-list .icon-gap { width: 22px; flex: none; }
</style>
</head>
<body>

<section class="card card--front" aria-label="Card front">
  <div class="brand-mark" aria-hidden="true"></div>
  <div class="wordmark">
    <div class="wordmark__main">MERIDIAN</div>
    <div class="wordmark__sub">Crestline Motors</div>
  </div>
  <div class="lime-edge"></div>
</section>

<section class="card card--back" aria-label="Card back">
  <div class="brand-mark" aria-hidden="true"></div>
  <div class="monogram">MCM</div>

  <div class="name-tab">
    <div class="name-tab__name">Darnell R Okonski</div>
    <div class="name-tab__role">Owner</div>
  </div>

  <ul class="contact-list">
    <li>(555) 304-6618
      <svg viewBox="0 0 24 24" aria-hidden="true"><path fill="#b6d31a" d="M6.6 10.8c1.4 2.8 3.8 5.1 6.6 6.6l2.2-2.2c.3-.3.7-.4 1-.2 1.1.4 2.3.6 3.6.6.6 0 1 .4 1 1V20c0 .6-.4 1-1 1C10.6 21 3 13.4 3 4c0-.6.4-1 1-1h3.5c.6 0 1 .4 1 1 0 1.3.2 2.5.6 3.6.1.3 0 .7-.2 1z"/></svg>
    </li>
    <li>mercrestmotors@quillbox.example
      <svg viewBox="0 0 24 24" aria-hidden="true"><rect x="2.5" y="5" width="19" height="14" rx="1" fill="none" stroke="#b6d31a" stroke-width="2"/><path d="M3 6l9 7 9-7" fill="none" stroke="#b6d31a" stroke-width="2"/></svg>
    </li>
    <li>Dealer Lic # 48265<span class="icon-gap"></span></li>
  </ul>

  <div class="lime-edge"></div>
</section>

</body>
</html>
```